Industry automation wholesale website

www.velturo.eu provides solutions for automation, building automation and digital signage.

Our products are rugged, reliable, energy saving and representative.

Scope of pages:
● welcome page
- scope of products
- applications, success stories and news
● category page
- short introduction
- sub categories
- product highlights
● product page
- short introduction
- about 3 to 4 pictures
- technical specifications: materials, dimensions
- price
- related products

Optional:
● contact page
- address
- contact form
● blog
- picture
- text
● logo
● favicon / apple touch icon

Conclusion:
● We need a professionally looking site
● Bright colors (e.g. white, grey, metalic colors, blue)

some pages we like:
http://www.prandek.de/
http://www.morvalix.de/

Target Market(s)

Our target market is the industrial sector
● Target audience: engineering and IT professionals

Industry/Entity Type

Building

Requirements
Must have
• ● only use free available fonts e.g. Lumara Type Library (http://www.lumaratype.com/webfonts)
Should not have
• ● sound
● flash

```html
<!DOCTYPE html>
<html lang="en">
<head>
<meta charset="utf-8">
<title>velturo – Partner for Industrial Automation</title>
<link rel="stylesheet" href="https://fonts.googleapis.com/css2?family=PT+Sans:wght@400;700&family=PT+Sans+Narrow:wght@400;700&display=swap">
<style>
:root{
  --navy:#0e5478;
  --blue:#2a7aa6;
  --footer:#23709c;
  --footer-box:#0f5175;
  --footer-bottom:#125a80;
  --brand:#1d6c93;
  --orange:#e0542a;
  --grey-text:#4a4a4a;
  --head-grey:#555b60;
  --line:#9a9a9a;
  --panel:#dfe7e9;
  --white:#fff;
}
*{margin:0;padding:0;box-sizing:border-box}
html,body{width:1008px;height:1200px;overflow:hidden;background:#fff}
body{position:relative;font-family:"PT Sans",Arial,sans-serif;color:var(--grey-text)}
.abs{position:absolute}
.topbar{left:0;top:0;width:1008px;height:30px;background:var(--navy)}
.flags{right:81px;top:7px;display:flex;gap:6px}
.flags svg{display:block}
.header{left:0;top:30px;width:1008px;height:116px;background:#fff}
.brand{left:77px;top:44px;display:flex;align-items:center;gap:10px}
.brand-name{font-size:58px;font-weight:400;color:var(--brand);letter-spacing:1px;line-height:1}
.brand-mark{width:34px;height:34px;border-radius:50%;background:var(--brand)}
.brand-tag{left:77px;top:102px;font-size:15px;color:var(--brand)}
.search{left:725px;top:82px;width:201px;height:33px;border:1px solid #cfd4d7;font-size:13px;color:#8c9296;padding:8px 12px}
.search svg{position:absolute;right:8px;top:9px}
.nav{left:0;top:146px;width:1008px;height:42px;background:var(--blue)}
.nav ul{list-style:none;display:flex;gap:13px;position:absolute;left:77px;top:13px}
.nav li{color:#fff;font-size:12.5px;text-transform:uppercase}
.hero{left:0;top:188px;width:1008px;height:284px;background:linear-gradient(90deg,#3f4a56 0%,#8e99a4 35%,#b7bec6 55%,#5c6570 80%,#c7ccd2 100%)}
.hero-title{left:181px;top:248px;background:rgba(200,205,210,.75);color:rgba(110,115,120,.9);font-size:40px;font-weight:700;padding:0 10px;line-height:44px}
.hero-sub{left:181px;top:310px;background:rgba(160,168,176,.5);color:rgba(200,205,210,.95);font-size:26px;font-weight:700;padding:2px 8px}
.arrow{width:58px;height:58px;border-radius:50%;background:rgba(40,45,50,.35);top:281px}
.arrow svg{position:absolute;left:17px;top:15px}
.caption{left:0;top:435px;width:1008px;height:37px;background:rgba(60,60,60,.35);color:#fff;font-size:19px;padding:5px 0 0 79px}
.tabs{left:81px;top:486px;width:624px;height:85px;border:1px solid #d6d6d6;background:linear-gradient(#fff,#ececec);display:flex}
.tab{display:flex;align-items:center;gap:8px;padding-left:10px;border-right:1px solid #d0d0d0;font-family:"PT Sans Narrow",sans-serif;font-weight:700;color:var(--orange);font-size:13px;line-height:17px;text-transform:uppercase}
.tab:last-child{border-right:0}
.thumb{width:60px;height:60px;border-radius:50%;border:3px solid #d8e2e8;flex:none}
.tab-pointer{left:172px;top:570px}
.chip{left:109px;top:596px;width:220px;height:220px;border-radius:50%;border:8px solid #6e9bb8;background:radial-gradient(circle at 45% 45%,#3b4a3e,#2d6a3a 55%,#1f4a2a);box-shadow:0 0 0 3px #d0dde5}
.section-title{left:392px;top:592px;font-family:"PT Sans Narrow",sans-serif;font-weight:700;font-size:24px;line-height:26px;color:var(--head-grey)}
.section-text{left:392px;top:664px;width:316px;font-size:10.4px;line-height:15.8px;color:#333}
.rule{height:1px;background:var(--line)}
.highlight{left:395px;top:794px;font-size:28px;font-weight:700;color:var(--brand)}
.view-more{left:641px;top:839px;font-family:"PT Sans Narrow",sans-serif;font-weight:700;font-size:13px;color:var(--orange)}
.quote{left:720px;top:486px;width:202px;height:270px;background:var(--panel);padding:14px 18px}
.quote h2{font-family:"PT Sans Narrow",sans-serif;font-size:18px;color:var(--orange);margin-bottom:10px}
.field{background:#fff;border:1px solid #cfd6d8;height:24px;font-size:11px;color:#b8bec0;padding:4px 5px;margin-bottom:4px}
.field.tall{height:76px}
.submit{display:inline-block;margin-top:8px;background:var(--orange);color:#fff;font-weight:700;font-size:12px;padding:4px 15px;border-radius:2px}
.partner{left:719px;top:767px;width:203px;height:83px;background:linear-gradient(135deg,#2e3a47,#7c8a97 55%,#c3ccd4)}
.partner span{position:absolute;left:0;bottom:0;width:100%;height:22px;background:rgba(120,130,140,.7);color:#fff;font-family:"PT Sans Narrow",sans-serif;font-size:16px;text-align:center;line-height:22px}
.footer{left:0;top:890px;width:1008px;height:263px;background:var(--footer)}
.fbox{top:917px;width:290px;height:206px;background:var(--footer-box);padding:26px 24px;color:#fff}
.fbox h3{font-weight:400;font-size:17px;margin-bottom:18px}
.input{background:#ececec;color:#333;font-size:14px;height:22px;width:231px;padding:1px 14px;margin-bottom:21px}
.btn{display:inline-block;background:#07304a;color:#fff;font-size:14px;padding:3px 12px;width:97px;margin-top:4px}
.testi p{font-size:11px;line-height:19px;color:#9bbcd0}
.testi .who{color:#d2e2ec;margin-top:10px;font-family:Georgia,serif}
.dots{right:16px;top:28px;display:flex;gap:6px}
.dots i{width:13px;height:13px;border-radius:50%;background:#7f9fb4;display:block}
.contact{left:713px;top:914px;color:#fff}
.contact h3{font-weight:400;font-size:17px}
.crow{display:flex;align-items:center;gap:10px;font-size:11px;margin-top:16px}
.cicon{width:40px;height:40px;border-radius:50%;background:#6d9ab6;display:flex;align-items:center;justify-content:center}
.social{display:flex;gap:7px;margin-top:10px}
.social i{width:24px;height:24px;border-radius:50%;background:#8a9aa6;display:block}
.bottom{left:0;top:1153px;width:1008px;height:47px;background:var(--footer-bottom);color:#fff;font-size:9.5px;text-align:center;line-height:47px}
</style>
</head>
<body>
<div class="abs topbar"></div>
<div class="abs flags" aria-label="Language selection">
  <svg width="18" height="12"><rect width="6" height="12" fill="#1f3f9c"/><rect x="6" width="6" height="12" fill="#fff"/><rect x="12" width="6" height="12" fill="#d8262c"/></svg>
  <svg width="18" height="12"><rect width="18" height="4" fill="#000"/><rect y="4" width="18" height="4" fill="#d8262c"/><rect y="8" width="18" height="4" fill="#f5c400"/></svg>
  <svg width="18" height="12"><rect width="6" height="12" fill="#1e8a3c"/><rect x="6" width="6" height="12" fill="#fff"/><rect x="12" width="6" height="12" fill="#d8262c"/></svg>
  <svg width="18" height="12"><rect width="7" height="12" fill="#1e7a3c"/><rect x="7" width="11" height="12" fill="#d8262c"/><circle cx="7" cy="6" r="2.5" fill="#f5c400"/></svg>
  <svg width="18" height="12"><rect width="18" height="12" fill="#d8262c"/><rect y="3" width="18" height="6" fill="#f5c400"/></svg>
  <svg width="18" height="12"><rect width="18" height="12" fill="#fff"/><circle cx="9" cy="6" r="3.5" fill="#d8262c"/></svg>
  <svg width="18" height="12"><rect width="18" height="12" fill="#d8262c"/></svg>
</div>

<header class="abs header"></header>
<div class="abs brand"><span class="brand-name">velturo</span><span class="brand-mark"></span></div>
<div class="abs brand-tag">analog digital measurements</div>
<div class="abs search">Product Search
  <svg width="16" height="16" viewBox="0 0 16 16"><circle cx="6.5" cy="6.5" r="4.5" fill="none" stroke="#9aa0a4" stroke-width="1.5"/><line x1="10" y1="10" x2="14.5" y2="14.5" stroke="#9aa0a4" stroke-width="2"/></svg>
</div>

<nav class="abs nav"><ul><li>Home</li><li>Products</li><li>Contact</li><li>Search</li><li>Shopping Cart</li></ul></nav>

<section class="abs hero" role="img" aria-label="Photo of a business team with a man in a suit reaching out for a handshake"></section>
<div class="abs hero-title">Partner</div>
<div class="abs hero-sub">for Industrial Automation</div>
<div class="abs arrow" style="left:70px"><svg width="24" height="28"><polyline points="16,4 6,14 16,24" fill="none" stroke="#ccc" stroke-width="5"/></svg></div>
<div class="abs arrow" style="left:866px"><svg width="24" height="28"><polyline points="8,4 18,14 8,24" fill="none" stroke="#ccc" stroke-width="5"/></svg></div>
<div class="abs caption">velturo® is based in Germany and guaranty quick and reliable service.</div>

<div class="abs tabs">
  <div class="tab" style="width:203px"><span class="thumb" role="img" aria-label="Remote IO modules" style="background:#4f86b8"></span>Modbus RTU / RS485<br>Remote IO Modules</div>
  <div class="tab" style="width:216px"><span class="thumb" role="img" aria-label="Touch panel computer" style="background:#8fa9c4"></span>Touch Panel<br>Industry Computer</div>
  <div class="tab" style="width:205px"><span class="thumb" role="img" aria-label="Embedded system box" style="background:#9ea4aa"></span>Embedded Systems<br>for Industrial<br>Automation</div>
</div>
<svg class="abs tab-pointer" width="20" height="11"><polygon points="0,0 20,0 10,10" fill="#ececec" stroke="#d6d6d6"/></svg>

<div class="abs chip" role="img" aria-label="Close-up photo of an embedded circuit board"></div>
<h1 class="abs section-title">EMBEDDED SYSTEMS FOR<br>INDUSTRIAL AUTOMATION</h1>
<p class="abs section-text">RS485 Remote IO modules are ideal to realize decentralized distributed IO units over long distances. We provide the whole product range form Remote IO Modules with RS485 Bus and Modbus RTU such as analogue IO Modules, digital IO Modules, Relay Modules and Timer / Counter Modules. Also we provide RS422 and RS485 converter to RS232, USB, TCP/IP.</p>
<div class="abs rule" style="left:392px;top:776px;width:313px"></div>
<div class="abs highlight">RS232, USB, TCP/IP</div>
<div class="abs rule" style="left:81px;top:850px;width:554px"></div>
<div class="abs view-more">VIEW MORE</div>

<aside class="abs quote">
  <h2>GET FREE QUOTE</h2>
  <div class="field">Name</div>
  <div class="field">Email Id</div>
  <div class="field">Subject</div>
  <div class="field tall">Description</div>
  <span class="submit">Submit</span>
</aside>
<div class="abs partner" role="img" aria-label="Photo of two business people shaking hands"><span>PARTNER WITH US</span></div>

<footer class="abs footer"></footer>
<div class="abs fbox" style="left:78px">
  <h3>Subscribe to our weekly newsletter</h3>
  <div class="input">Your name</div>
  <div class="input">Email ID</div>
  <span class="btn">Subscribe</span>
</div>
<div class="abs fbox testi" style="left:385px">
  <h3>Testimoanials</h3>
  <div class="abs dots"><i></i><i></i></div>
  <p>Lorem Ipsum is simply dummy text of the printing and typesetting industry. Lorem Ipsum has been the industr standard dummy text ever since the 1500s, when an unknown printer took a</p>
  <p class="who">Lorem Ipsum is simply<br>Owner, Lorem Ipsum</p>
</div>
<div class="abs contact">
  <h3>Contact</h3>
  <div class="crow"><span class="cicon"><svg width="20" height="16" viewBox="0 0 20 16"><path d="M2 6c0-3 16-3 16 0v2h-4V6H6v2H2z" fill="#3d5566"/><rect x="4" y="9" width="12" height="6" rx="1" fill="#3d5566"/></svg></span>+49 - 211 - 504 27 19</div>
  <div class="crow"><span class="cicon"><svg width="18" height="13" viewBox="0 0 18 13"><rect width="18" height="13" fill="#f2e3b0"/><polyline points="0,0 9,7 18,0" fill="none" stroke="#b8a36a"/></svg></span>info@velturo.de</div>
  <h3 style="margin-top:26px">Connect with us</h3>
  <div class="social" aria-label="Social networks"><i></i><i></i><i></i><i></i><i></i></div>
</div>
<div class="abs bottom">© 2014velturo.com. All Rights Reserved.</div>
</body>
</html>
```